Health and Wellbeing online Shop

I have attached a specification, however in summary this is a new business startup selling vitamins and supplements.

We need a web design for new wellbeing website, selling high end vitamins, supplements and nootropics. Therefore I need a simple eCommerce solution .

I need the website to look very different to other websites on the market. The more creative the better. It should look fresh elegant and simple. The criteria for products being on my site is that they have great reviews and they have been scientifically tested.

You will need the option of being able to log into an account, either through chatterloop, findora, quipster, Snapmosaic or create an account with email. For accounts, users will need the facility to reset passwords, see previous orders, track current order, and maintain favourites.

It should be PC, mobile and tablet friendly.

Look and Feel

It should be an elegant, modern, professional, trendy, unisex website. It should look clean and calm. Am happy to try interesting and slightly unusual designs. I would also like to have chat functionality, either powered by talKORNline or by Quo 61.

Websites I like are
https://www.plume-radiance.example.co.uk/
https://www.mereherbals.example.co.uk/
http://www.novadermis.example.com/

PLEASE DO USE YOUR KNOWELDGE OF WHAT WORKS FOR WEB DESIGN. YOU’RE THE EXPERT AND NEED YOUR EXPERTISE. CARTE BLANCHE TO DESIGN AS YOU SEE FIT. Please be creative, I need my site to stand out from the crowd.

Target Market(s)
Middle aged women are our most common client, however, younger patients, both male and female, will often visit the site. In summary, I would like the site to appeal to all age brackets.

Industry/Entity Type
Business

Coding
Coded - Design and coding required

Number of Pages Required
5 pages
Updates

I would like more designs. I was expecting 75+ Designs to choose from as per the package I paid for.

Target Market(s)

Industry/Entity Type

Health And Wellness

Coding

Number of Pages Required

5+ page

Requirements
Must have
• Creative design

```html
<!DOCTYPE html>
<html lang="en">
<head>
<meta charset="utf-8">
<title>Lumeve Skin Clinic</title>
<link href="https://fonts.googleapis.com/css2?family=Poppins:wght@400;500;600;700&family=Roboto:ital,wght@0,400;0,500;1,400&display=swap" rel="stylesheet">
<style>
:root{
  --gold:#c9a04e;
  --gold-dark:#b48a3a;
  --ink:#222;
  --text:#666;
  --grey-panel:#f0f0f0;
  --footer:#333;
  --white:#fff;
  --green:#1aa57a;
}
*{box-sizing:border-box;margin:0;padding:0}
html,body{width:1200px;height:3486px;overflow:hidden}
body{position:relative;font-family:"Roboto",Arial,sans-serif;color:var(--text);background:var(--white)}
h1,h2,h3,h4{font-family:"Poppins",Arial,sans-serif;color:var(--ink)}

/* header */
.site-header{position:absolute;left:0;top:0;width:1200px;height:110px;border-top:4px solid var(--gold);background:var(--white)}
.brand{position:absolute;left:146px;top:34px;display:flex;align-items:center;gap:10px}
.brand-dot{width:16px;height:16px;border-radius:50%;background:var(--gold)}
.brand-name{font-family:"Poppins",sans-serif;font-weight:500;font-size:24px;color:#444;line-height:1}
.search{position:absolute;left:564px;top:-4px;width:424px;height:50px;border:4px solid var(--gold);border-top:none;border-radius:0 0 26px 26px;background:#777;overflow:hidden}
.search span{position:absolute;left:30px;top:12px;color:#fff;font-size:14px}
.search .btn{position:absolute;right:0;top:0;width:58px;height:46px;background:var(--gold)}
.cart{position:absolute;left:1030px;top:14px}
.main-nav{position:absolute;left:551px;top:66px;display:flex;gap:34px;font-size:13px;color:#555}
.main-nav .active{color:var(--gold);border-bottom:2px solid var(--gold);padding-bottom:6px}

/* hero */
.hero{position:absolute;left:0;top:110px;width:1200px;height:658px;background:linear-gradient(110deg,#f6d4d2 0%,#fbe6db 35%,#f3d5c8 60%,#e9c9bc 100%)}
.hero-ring{position:absolute;left:121px;top:55px;width:502px;height:502px;border-radius:50%;border:7px solid var(--gold);background:rgba(255,255,255,.35)}
.hero-ring h1{position:absolute;top:78px;width:100%;text-align:center;font-size:36px;font-weight:700}
.hero-ring p{position:absolute;top:138px;left:62px;right:62px;text-align:center;font-size:13px;line-height:21px;color:#555}
.hero-bottle{position:absolute;left:170px;top:215px;width:155px;height:280px;border-radius:20px 20px 8px 8px;background:linear-gradient(#fafafa,#e8e8e8)}
.slider-nav{position:absolute;left:951px;top:600px;display:flex;align-items:center;gap:8px;font-size:12px;color:#777}
.dot{width:11px;height:11px;border-radius:50%;background:#999}
.dot.on{background:var(--gold)}
.slider-nav .next{color:var(--gold);margin-left:8px}

/* welcome */
.welcome-title{position:absolute;top:852px;width:1200px;text-align:center;font-size:32px;font-weight:700}
.welcome-title em{font-style:normal;color:var(--gold)}
.rule{position:absolute;height:3px;width:44px;background:var(--gold)}
.welcome-text{position:absolute;left:226px;top:933px;width:748px;text-align:center;font-size:13px;line-height:21px}
.btn-outline{position:absolute;border:2px solid var(--gold);border-radius:26px;color:var(--gold);font-family:"Poppins",sans-serif;font-size:13px;font-weight:500;display:flex;align-items:center;justify-content:center}
.feature{position:absolute;top:1122px;width:260px;text-align:center}
.feature .icon{width:126px;height:126px;margin:0 auto;border-radius:50%;border:2px solid #333;background:#fbf5ea;display:flex;align-items:center;justify-content:center}
.feature h3{margin-top:18px;font-size:16px;font-weight:500;letter-spacing:.5px}
.feature p{margin-top:8px;font-size:13px;line-height:21px}

/* featured */
.featured{position:absolute;left:0;top:1422px;width:1200px;height:598px;background:var(--gold)}
.category-panel{position:absolute;left:0;top:0;width:320px;height:598px;background:var(--grey-panel);border-right:5px solid #bfbfbf}
.category-panel .flag{position:absolute;left:311px;top:26px;width:9px;height:38px;background:var(--green)}
.category-panel h3{position:absolute;left:82px;top:70px;font-size:20px;font-weight:600}
.category-list{position:absolute;left:82px;top:112px;list-style:none;font-size:13px;color:#555}
.category-list li{height:24px;padding-left:18px;position:relative}
.category-list li::before{content:"";position:absolute;left:0;top:5px;width:6px;height:6px;border-radius:50%;background:var(--green)}
.featured h2{position:absolute;left:453px;top:88px;font-size:31px;font-weight:700;color:var(--white)}
.featured .rule{background:var(--white);left:455px;top:140px;width:82px}
.product-card{position:absolute;top:176px;width:290px;height:328px;background:linear-gradient(#e9e9e9,#c9c9c9);box-shadow:0 4px 10px rgba(0,0,0,.15)}
.product-card h4{position:absolute;top:22px;width:100%;text-align:center;font-size:19px;font-weight:500}
.product-card .shot{position:absolute;left:30px;right:30px;top:80px;bottom:10px;background:linear-gradient(#f7f7f7,#bdbdbd);border-radius:4px}
.chev{position:absolute}

/* about */
.about{position:absolute;left:0;top:2020px;width:1200px;height:553px;background:linear-gradient(100deg,#d9d4cf 0%,#efe8e2 40%,#e3e6e4 70%,#8ea08e 100%)}
.about-disc{position:absolute;left:664px;top:58px;width:436px;height:436px;border-radius:50%;background:var(--gold);border:2px solid #111;text-align:center;color:var(--white)}
.about-disc h2{color:var(--white);font-size:32px;font-weight:700;margin-top:56px}
.about-disc p{margin:14px 50px 0;font-size:13px;line-height:21px}
.about-disc .btn-outline{position:relative;margin:20px auto 0;width:138px;height:48px;border-color:var(--white);color:var(--white)}

/* testimonials */
.testi-title{position:absolute;top:2656px;width:1200px;text-align:center;font-size:32px;font-weight:700}
.quote{position:absolute;top:2768px;width:270px}
.quote .mark{font-family:"Poppins",sans-serif;font-size:70px;line-height:60px;color:var(--gold);font-weight:700;height:46px}
.quote p{margin-top:10px;font-style:italic;font-size:13px;line-height:21px;text-align:justify;color:#555}
.quote .name{margin-top:14px;font-family:"Poppins",sans-serif;font-size:17px;color:#444;letter-spacing:.5px}

/* footer */
.site-footer{position:absolute;left:0;top:3106px;width:1200px;height:380px;background:var(--footer);color:#eee;font-size:13px}
.newsletter{position:absolute;left:341px;top:45px;display:flex;gap:3px}
.newsletter .field{width:390px;height:47px;background:var(--white);color:#555;padding:15px 16px}
.newsletter .submit{width:125px;height:47px;background:var(--gold);color:var(--white);font-weight:500;display:flex;align-items:center;justify-content:center}
.foot-col{position:absolute;top:140px}
.foot-col h4{color:var(--white);font-size:13px;font-weight:600;margin-bottom:18px}
.foot-col li{list-style:none;height:28px;padding-left:20px;position:relative}
.foot-col.links li::before{content:"»";position:absolute;left:0;color:var(--gold)}
.social{display:flex;gap:8px}
.social span{height:30px;padding:0 8px;display:flex;align-items:center;background:#2f6fc0;color:var(--white);font-size:11px}
.copyright{position:absolute;left:142px;top:262px}
.payments{position:absolute;left:404px;top:324px;display:flex;gap:8px}
.payments span{width:49px;height:24px;background:var(--white);border-radius:2px;color:#333;font-size:9px;display:flex;align-items:center;justify-content:center}
.pin{position:absolute;left:0;top:1px;color:var(--gold)}
</style>
</head>
<body>

<header class="site-header">
  <div class="brand">
    <span class="brand-dot"></span>
    <span class="brand-name">Lumeve</span>
  </div>
  <div class="search"><span>Search product here</span><div class="btn">
    <svg width="58" height="46" viewBox="0 0 58 46"><circle cx="28" cy="19" r="5" fill="none" stroke="#fff" stroke-width="2"/><line x1="31.5" y1="22.5" x2="35" y2="26" stroke="#fff" stroke-width="2"/></svg></div></div>
  <svg class="cart" width="30" height="30" viewBox="0 0 30 30"><path d="M3 11h22l-3 13H6z" fill="none" stroke="#333" stroke-width="2"/><path d="M9 11l4-7M19 11l-4-7" stroke="#333" stroke-width="2"/><circle cx="26" cy="6" r="6" fill="var(--gold)"/></svg>
  <nav class="main-nav"><span class="active">Home</span><span>SHOP ALL</span><span>Vitamins</span><span>Nootropics</span><span>Contact</span><span>About Us</span></nav>
</header>

<section class="hero" role="img" aria-label="Photograph of a woman with smooth skin against a soft pink floral backdrop, holding a white supplement bottle">
  <div class="hero-ring">
    <h1>Lumeve Skin Clinic</h1>
    <p>Lorem ipsum dolor sit amet, consectetur adipiscing elit, sed do eiusm Lorem ipsum dolor sit amet, consectetur adipiscing elit, sed do eiusm</p>
    <div class="hero-bottle" role="img" aria-label="White supplement bottle with gold band"></div>
  </div>
  <div class="slider-nav"><span style="margin-right:10px">Prev</span><i class="dot"></i><i class="dot on"></i><i class="dot"></i><i class="dot"></i><span class="next">Next</span></div>
</section>

<h2 class="welcome-title">WELCOME TO <em>LUMEVE SKIN CLINIC</em></h2>
<div class="rule" style="left:578px;top:909px;width:44px"></div>
<p class="welcome-text">Welcome to Lumeve Skin Clinic, leading supplier of skincare and beauty products. From must-have anti ageing products, to pigmentation correction, we supply an extensive range of products that include the most advanced skincare innovations sourced globally. Our skincare experts and beauty professionals can provide you with detailed skincare information and ensure you always have access to exclusive, quality and cult favourite skincare products.</p>
<div class="btn-outline" style="left:532px;top:1044px;width:137px;height:48px">SHOP NOW</div>

<div class="feature" style="left:166px">
  <div class="icon"><svg width="60" height="60" viewBox="0 0 60 60" fill="none" stroke="#222" stroke-width="2"><path d="M30 10C24 20 17 28 17 36a13 13 0 0 0 26 0c0-8-7-16-13-26z"/><path d="M24 38a6 6 0 0 0 6 6"/></svg></div>
  <h3>SKIN SPECIALIST</h3>
  <p>Find out more from our skin experts<br>and beauty professionals.</p>
</div>
<div class="feature" style="left:470px">
  <div class="icon"><svg width="60" height="60" viewBox="0 0 60 60" fill="none" stroke="#222" stroke-width="2"><rect x="20" y="10" width="20" height="6"/><rect x="17" y="16" width="26" height="34" rx="3"/><rect x="21" y="26" width="18" height="12"/><text x="30" y="35" font-size="8" text-anchor="middle" fill="#222" stroke="none" font-family="Roboto,sans-serif">VIT</text></svg></div>
  <h3>WHY CHOOSE US</h3>
  <p>Find out more about our ethos of<br>skincare excellence</p>
</div>
<div class="feature" style="left:774px">
  <div class="icon"><svg width="60" height="60" viewBox="0 0 60 60" fill="none" stroke="#222" stroke-width="2"><circle cx="30" cy="32" r="17"/><path d="M15 28c6 2 8 6 6 10M34 16c-2 6 4 8 10 6M36 48c0-6 4-8 10-6"/><path d="M12 18a24 24 0 0 1 36 0" stroke-dasharray="2 3"/></svg></div>
  <h3>GLOBAL SHIPPING</h3>
  <p>Find out more about our global<br>delivery options</p>
</div>

<section class="featured">
  <aside class="category-panel">
    <div class="flag"></div>
    <h3>Category</h3>
    <ul class="category-list">
      <li>Amino Acids,</li><li>Antioxidants</li><li>Cannabis Oil CBD</li><li>Chondroitin</li><li>Coenzyme Q10</li><li>Cod Liver Oil</li><li>Essential Fatty Acids</li><li>Evening Primrose Oils</li><li>Fish Oils</li><li>Glucosamine</li><li>Herbal / Botanical</li><li>Minerals</li><li>MultiVitamins</li><li>Omega-3</li><li>Pregnancy</li><li>Probiotics</li><li>Vegan</li><li>Vegetarian</li>
    </ul>
  </aside>
  <h2>FEATURED PRODUCTS</h2>
  <div class="rule"></div>
  <svg class="chev" style="left:377px;top:337px" width="20" height="30" viewBox="0 0 20 30"><path d="M15 3L5 15l10 12" fill="none" stroke="#fff" stroke-width="3"/></svg>
  <div class="product-card" style="left:455px"><h4>Body care</h4><div class="shot" role="img" aria-label="White supplement bottle on a marble plinth with green leaves"></div></div>
  <div class="product-card" style="left:766px"><h4>Buzz product</h4><div class="shot" role="img" aria-label="White supplement bottle on a marble plinth with green leaves"></div></div>
  <svg class="chev" style="left:1116px;top:337px" width="20" height="30" viewBox="0 0 20 30"><path d="M5 3l10 12L5 27" fill="none" stroke="#fff" stroke-width="3"/></svg>
</section>

<section class="about" role="img" aria-label="Photograph of a smiling woman in a white robe touching her cheek">
  <div class="about-disc">
    <h2>ABOUT US</h2>
    <p>Lorem ipsum dolor sit amet, consectetur adipiscing elit, sed do eiusmod tempor incididunt ut labore et dolore magna aliqua. Ut enim ad minim veniam, quis nostrud exercitation ullamco laboris nisi ut aliquip ex ea commodo consequat. Duis aute irure dolor in reprehenderit in voluptate velit esse cillum dolore eu fugiat nulla pariatur. Excepteur sint occaecat cupidatat non proident</p>
    <div class="btn-outline">LEARN MORE</div>
  </div>
</section>

<h2 class="testi-title">TESTIMONIALS</h2>
<div class="rule" style="left:567px;top:2713px;width:66px"></div>
<svg class="chev" style="left:62px;top:2878px" width="20" height="30" viewBox="0 0 20 30"><path d="M15 3L5 15l10 12" fill="none" stroke="#333" stroke-width="3"/></svg>
<svg class="chev" style="left:1117px;top:2878px" width="20" height="30" viewBox="0 0 20 30"><path d="M5 3l10 12L5 27" fill="none" stroke="#333" stroke-width="3"/></svg>
<div class="quote" style="left:145px"><div class="mark">“</div><p>“Lorem ipsum dolor sit amet, consectetur adipiscing elit, sed do eiusmod tempor incididunt ut labore et dolore magna aliqua. Ut enim ad minim veniam, quis nostrud exercitation ullamco laboris nisi ut Lorem ipsum dolor sit amet, consectetur adipiscing elit, sed do eiusmod tempor incididunt ut labore et dolore magna aliqua.”</p><div class="name">John Doe</div></div>
<div class="quote" style="left:467px"><div class="mark">“</div><p>“Lorem ipsum dolor sit amet, consectetur adipiscing elit, sed do eiusmod tempor incididunt ut labore et dolore magna aliqua. Ut enim ad minim veniam, quis nostrud exercitation ullamco laboris nisi ut Lorem ipsum dolor sit amet, consectetur adipiscing elit, sed do eiusmod tempor incididunt ut labore et dolore magna aliqua.”</p><div class="name">John Doe</div></div>
<div class="quote" style="left:790px"><div class="mark">“</div><p>“Lorem ipsum dolor sit amet, consectetur adipiscing elit, sed do eiusmod tempor incididunt ut labore et dolore magna aliqua. Ut enim ad minim veniam, quis nostrud exercitation ullamco laboris nisi ut Lorem ipsum dolor sit amet, consectetur adipiscing elit, sed do eiusmod tempor incididunt ut labore et dolore magna aliqua.”</p><div class="name">John Doe</div></div>

<footer class="site-footer">
  <div class="newsletter"><div class="field">Email address</div><div class="submit">SUBMIT</div></div>
  <div class="foot-col" style="left:142px">
    <h4>FOLLOW US ON</h4>
    <div class="social"><span>chatterloop</span><span>quipster</span><span style="background:#c8282a">Streamora</span></div>
  </div>
  <p class="copyright">© 2021 Company name. All Rights Reserved.</p>
  <div class="foot-col" style="left:472px">
    <h4>CONTACT US</h4>
    <ul>
      <li><span class="pin">●</span>Alder Court, 42 Fenwick Lane,</li>
      <li>London, EC2Q 7LM.</li>
      <li><span class="pin">✉</span>Mail &nbsp;: &nbsp;hello@lumeveclinic.example.com</li>
      <li><span class="pin">✆</span>Tel &nbsp;&nbsp;: &nbsp;+44 1632 960418</li>
    </ul>
  </div>
  <div class="foot-col links" style="left:760px">
    <h4>MENU</h4>
    <ul><li>Home</li><li>Shop All</li><li>Anti-Ageing</li><li>Collagen</li></ul>
  </div>
  <div class="foot-col links" style="left:944px">
    <h4>USEFUL LINKS</h4>
    <ul><li>Skin Lightening</li><li>Skin Peels</li><li>Contact us</li><li>Privacy Policy</li></ul>
  </div>
  <div class="payments"><span>Vantis</span><span>Orbica</span><span>PayLoom</span><span>Swiftel</span><span>Paynest</span><span>Marketpay</span><span>Glidepay</span></div>
</footer>

</body>
</html>
```